New Business Card Design Project

We require a business card design for Vexalund, a newly established Indian company.
Our focus is on the development, manufacturing, and export of a diverse array of pharmaceutical products on a global scale. The card should convey a professional appearance, as our primary markets are in Africa, China, and Southeast Asian nations.
We envision a two-sided business card, with the reverse side dedicated to a logo set against a solid color or an elegantly designed pattern. The corners should be rounded. We would appreciate seeing both horizontal and vertical design options. We trust the designer to utilize their expertise in creating this design.

The content for the business card is included in the attached Word file.

Target Market(s)

Our primary markets are in Africa, China, and Southeast Asian, Latin America, Maldives, Sri Lanka

Industry/Entity Type

Pharmaceutical Manufacturing and Export

Contact Information for Business Card

Colors

Designer to choose colors to be used in the design.

Requirements
Must have
• The reverse side of the business card features solely the logo along with the tagline, "Care for Every Day."
Should not have
• The logo should not exceed two instances, encompassing both the front and back sides of the card.

```html
<!DOCTYPE html>
<html lang="en">
<head>
<meta charset="utf-8">
<title>Vexalund Business Card</title>
<link rel="stylesheet" href="https://fonts.googleapis.com/css2?family=Poppins:wght@600&family=Arimo:wght@400;700&display=swap">
<style>
  :root {
    --stage: #4a4a4a;
    --card-dark: #2d2d2d;
    --card-light: #ffffff;
    --brand-blue: #27a8e0;
    --brand-coral: #f0604b;
    --ink: #2a2a2a;
    --tagline: #f2f2f2;
  }
  * { box-sizing: border-box; margin: 0; padding: 0; }
  html, body { width: 1200px; height: 689px; overflow: hidden; }
  body {
    background: var(--stage);
    display: flex;
    align-items: center;
    justify-content: center;
    gap: 40px;
    font-family: "Arimo", Arial, sans-serif;
  }
  .card {
    position: relative;
    width: 520px;
    height: 297px;
    border-radius: 20px;
    overflow: hidden;
  }
  .card--back {
    background: var(--card-dark);
    display: flex;
    flex-direction: column;
    align-items: center;
    justify-content: center;
    gap: 18px;
  }
  .brand {
    display: flex;
    align-items: center;
    gap: 12px;
  }
  .brand__dot {
    width: 26px;
    height: 26px;
    border-radius: 50%;
    background: var(--brand-blue);
  }
  .brand__name {
    font-family: "Poppins", Arial, sans-serif;
    font-weight: 600;
    color: var(--brand-blue);
    font-size: 46px;
    letter-spacing: 0.5px;
    line-height: 1;
  }
  .tagline {
    color: var(--tagline);
    font-size: 14px;
    letter-spacing: 0.3px;
  }
  .card--front { background: var(--card-light); }
  .front__brand {
    position: absolute;
    left: 34px;
    top: 40px;
    font-family: "Poppins", Arial, sans-serif;
    font-weight: 600;
    color: var(--brand-blue);
    font-size: 48px;
    line-height: 1;
  }
  .front__mark {
    position: absolute;
    right: 40px;
    top: 58px;
    width: 150px;
    height: 150px;
    border-radius: 50%;
    background: var(--brand-blue);
  }
  .person {
    position: absolute;
    left: 36px;
    top: 116px;
  }
  .person__name {
    color: var(--brand-blue);
    font-weight: 700;
    font-size: 20px;
  }
  .person__role {
    color: var(--brand-coral);
    font-size: 13px;
    margin-top: 2px;
  }
  .address {
    margin-top: 12px;
    color: var(--ink);
    font-size: 13px;
    line-height: 1.35;
  }
  .contacts {
    list-style: none;
    margin-top: 12px;
    color: var(--ink);
    font-size: 13px;
    line-height: 1.5;
  }
  .contacts li { display: flex; align-items: center; gap: 8px; }
  .contacts svg { width: 12px; height: 12px; fill: var(--brand-blue); flex: none; }
</style>
</head>
<body>
  <section class="card card--back" aria-label="Card reverse">
    <div class="brand">
      <span class="brand__dot"></span>
      <span class="brand__name">Vexalund</span>
    </div>
    <p class="tagline">Care for Every Day</p>
  </section>

  <section class="card card--front" aria-label="Card front">
    <h1 class="front__brand">Vexalund</h1>
    <span class="front__mark"></span>
    <div class="person">
      <p class="person__name">Arun K. Methal</p>
      <p class="person__role">CEO</p>
      <p class="address">12, Lotus Colony, Nandpur<br>440021, India</p>
      <ul class="contacts">
        <li>
          <svg viewBox="0 0 24 24" aria-hidden="true"><path d="M6.6 10.8a15.1 15.1 0 0 0 6.6 6.6l2.2-2.2c.3-.3.7-.4 1-.2 1.1.4 2.3.6 3.6.6.6 0 1 .4 1 1V20c0 .6-.4 1-1 1A17 17 0 0 1 3 4c0-.6.4-1 1-1h3.5c.6 0 1 .4 1 1 0 1.3.2 2.5.6 3.6.1.3 0 .7-.2 1z"/></svg>
          +919800012345
        </li>
        <li>
          <svg viewBox="0 0 24 24" aria-hidden="true"><path d="M2 5h20v14H2zm2 2v.5l8 5 8-5V7l-8 5z"/></svg>
          amethal@vexalund.com
        </li>
        <li>
          <svg viewBox="0 0 24 24" aria-hidden="true"><circle cx="12" cy="12" r="10"/></svg>
          www.vexalund.com
        </li>
      </ul>
    </div>
  </section>
</body>
</html>
```